Modellprojekt in der Jugendhilfe sucht für Abschlussbroschüre ansprechendes Design
Zielgruppe
Wir sind ein Jugendhilfeträger und haben kürzlich ein dreijähriges Modellprojekt 'Prüfzeichen-Mitbestimmte Familienbegleitung' (Signet 'PZ_Zertifizierung' liegt anbei) beendet. Zielgruppen sind zum Einen Kinder und Jugendliche, die in Erziehungshilfe-Wohngruppen leben und zum Anderen Fach- und Führungskräfte in der Kinder- und Jugendhilfe. Über Ablauf und Schlussfolgerungen aus dem abgeschlossenen Modellprojekt soll eine 30-seitige Broschüre mit dem Titel 'Hier wächst Mitsprache' Untertitel 'Ein Wegbericht zum Prüfzeichen' Auskunft geben.
Aufgabenstellung
- Broschüre im DIN A4 - Format,
- Dummy-Text für Projektstruktur und -beteiligte,
- Formschönes und dynamisches Design,
- Platzhalter für eigene Bilder (max. 3 pro Seite),
- die 6 Einrichtungslogos in einer Reihe auf dem Deckblatt vorne (unten),
- Der Broschüreninhalt ist in der PDF 'Kurzvorstellung enthalten',
- Vorgaben zum CD im PDF 'Hauptmanual KWB',
- Das KWB-Signet, wie im Manual beschrieben,
- das ebenfalls hochgeladene Gütesiegel kommt auf das Deckblatt

```html
<!DOCTYPE html>
<html lang="de">
<head>
<meta charset="utf-8">
<title>Hier wächst Mitsprache – Broschüre</title>
<link href="https://fonts.googleapis.com/css2?family=Source+Sans+3:wght@400;600;700&display=swap" rel="stylesheet">
<style>
  :root{
    --blue:#1f6db5;
    --blue-light:#e3edf7;
    --green:#2e6a3c;
    --green-dark:#1f4d2b;
    --orange:#e3562a;
    --yellow:#f2c230;
    --text:#4a4f55;
    --bg:#e6e7e8;
    --paper:#ffffff;
  }
  *{box-sizing:border-box;margin:0;padding:0}
  html,body{width:1200px;height:1200px;overflow:hidden;background:var(--bg);font-family:"Source Sans 3",Arial,sans-serif;color:var(--text)}
  .stage{position:relative;width:1200px;height:1200px}
  .page{position:absolute;top:331px;width:380px;height:537px;background:var(--paper);overflow:hidden;box-shadow:0 6px 18px rgba(0,0,0,.12)}
  .page--left{left:20px}
  .page--right{left:400px;box-shadow:0 6px 18px rgba(0,0,0,.12), inset 10px 0 12px -10px rgba(0,0,0,.15)}
  .page--cover{left:800px}
  .abs{position:absolute}
  .photo{position:absolute;border:4px solid #fff;box-shadow:0 2px 6px rgba(0,0,0,.25)}
  .photo--warm{background:linear-gradient(135deg,#c98a6c,#8d4b3a 60%,#d9b39a)}
  .photo--light{background:linear-gradient(135deg,#d9c7b8,#a98a76 55%,#ece3da)}
  .chalkboard{background:radial-gradient(ellipse at 55% 40%,#3b7f49,var(--green) 55%,var(--green-dark))}
  .story-title{font-size:21px;font-weight:700;color:var(--blue)}
  .story-sub{font-size:10px;font-weight:700;color:var(--blue);line-height:1.25}
  .lead{font-size:8.5px;font-weight:700;color:var(--blue);line-height:1.3;margin-bottom:5px}
  .body{font-size:7px;line-height:1.45}
  .body p{margin-bottom:5px}
  .subhead{font-size:8px;font-weight:700;color:var(--blue);line-height:1.3;margin:6px 0 3px}
  .info-box{background:var(--blue-light);padding:22px 10px 10px}
  .tag{position:absolute;background:var(--yellow);color:#5a4300;font-size:8px;font-weight:700;padding:4px 8px;transform:rotate(-8deg);letter-spacing:.5px}
  .folio{position:absolute;left:28px;bottom:14px;font-size:6.5px;color:#8a9096}
  .note-card{background:var(--blue-light);padding:18px 10px 10px;box-shadow:0 2px 5px rgba(0,0,0,.15)}
  .pin{position:absolute;width:9px;height:9px;border-radius:50%;background:var(--orange)}
  .avatar{position:absolute;border-radius:50%;border:3px solid #fff;background:linear-gradient(135deg,#e2b99a,#9c6a4d)}
  .cover-title{position:absolute;left:0;right:0;top:365px;text-align:center;font-size:20px;font-weight:700;color:var(--blue);line-height:1.2}
  .seal{position:absolute;left:40px;top:262px;width:72px;height:72px;border-radius:50%;background:#fff;border:4px solid var(--green);box-shadow:0 0 0 3px #fff,0 0 0 5px var(--orange)}
  .seal__core{position:absolute;inset:12px;border-radius:50%;background:var(--green)}
  .partners{position:absolute;left:22px;right:18px;top:455px;display:flex;justify-content:space-between;align-items:center}
  .partner{display:flex;align-items:center;gap:4px;font-size:6px;font-weight:600;color:var(--blue);line-height:1.15;max-width:56px}
  .partner__mark{flex:0 0 9px;height:9px;background:var(--orange)}
  .partner--main{font-size:13px;font-weight:700;max-width:none}
  .partner--main .partner__mark{flex-basis:14px;height:14px;background:var(--blue)}
</style>
</head>
<body>
<div class="stage">

  <!-- Spread: left page -->
  <section class="page page--left">
    <div class="photo photo--warm" style="left:196px;top:112px;width:168px;height:116px" role="img" aria-label="Foto: Jugendliche sitzen gemeinsam in einer Wohngruppe"></div>

    <h2 class="story-title abs" style="left:28px;top:232px">Erfolgsstory</h2>
    <p class="story-sub abs" style="left:28px;top:262px;width:320px">Mitreden statt nur Best Practice – Beteiligung vor Ort,<br>z. B. Selbstvertretung in der Gruppe</p>

    <div class="abs" style="left:28px;top:298px;width:150px">
      <p class="lead">Unsere Gruppe plant Ausflüge jetzt gemeinsam mit allen.</p>
      <div class="body">
        <p>Jeden Monat treffen wir uns zum Gruppenabend. Dort sammeln wir Ideen und stimmen ab, wohin es geht.</p>
      </div>
    </div>
    <div class="photo photo--light" style="left:28px;top:392px;width:150px;height:104px" role="img" aria-label="Foto: Jugendliche lachen zusammen auf einem Sofa"></div>

    <div class="abs body" style="left:195px;top:298px;width:160px">
      <p>Wer eine Idee hat, schreibt sie auf eine Karte. Die Betreuenden helfen bei der Umsetzung und achten darauf, dass alle gehört werden.</p>
    </div>
    <div class="abs info-box" style="left:195px;top:370px;width:160px;height:128px">
      <div class="body">
        <p>1. Ideen sammeln und offen besprechen</p>
        <p>2. Gemeinsam abstimmen und Aufgaben verteilen</p>
        <p>3. Ergebnis festhalten und nach dem Ausflug auswerten</p>
      </div>
    </div>
    <span class="tag" style="left:186px;top:360px">Gut zu wissen</span>

    <p class="folio">12 &nbsp; Hier wächst Mitsprache – Ein Wegbericht zum Prüfzeichen</p>
  </section>

  <!-- Spread: right page -->
  <section class="page page--right">
    <div class="abs chalkboard" style="left:0;top:0;width:380px;height:230px" role="img" aria-label="Illustration: Kreidepfeile auf einer Tafel, die nach oben zeigen"></div>
    <svg class="abs" style="left:0;top:180px" width="380" height="70" viewBox="0 0 380 70">
      <path d="M0 40 Q190 10 380 28 L380 70 L0 70 Z" fill="#fff"/>
      <path d="M0 40 Q190 10 380 28" fill="none" stroke="var(--orange)" stroke-width="4"/>
    </svg>
    <div class="avatar" style="left:318px;top:150px;width:40px;height:40px" role="img" aria-label="Porträtfoto einer Fachkraft"></div>

    <div class="abs body" style="left:20px;top:240px;width:160px">
      <p>Im Projekt haben wir erlebt, wie viel Kraft entsteht, wenn junge Menschen mitentscheiden dürfen. Gespräche wurden offener und Regeln verständlicher.</p>
      <p class="subhead">Ab wann ist eine Gruppe wirklich beteiligt?</p>
      <p>Wenn Entscheidungen nicht nur erklärt, sondern gemeinsam getroffen werden.</p>
      <p class="subhead">Was braucht es dafür im Alltag?</p>
      <p>Feste Zeiten, klare Absprachen und Fachkräfte, die zuhören und Rückmeldung geben.</p>
    </div>

    <div class="abs note-card" style="left:200px;top:236px;width:160px;height:190px">
      <p class="lead">Das sagt die Gruppe</p>
      <div class="body">
        <p>„Früher wurde für uns entschieden, heute fragen die Betreuer zuerst uns. Das fühlt sich gut an.“</p>
        <p>„Beim Gruppenrat kann jeder etwas sagen, auch die Jüngsten.“</p>
      </div>
    </div>
    <span class="pin" style="left:276px;top:231px"></span>
  </section>

  <!-- Cover -->
  <section class="page page--cover">
    <div class="abs chalkboard" style="left:0;top:0;width:380px;height:300px" role="img" aria-label="Illustration: Kreidepfeile in alle Richtungen um ein Fragezeichen auf grüner Tafel"></div>
    <svg class="abs" style="left:0;top:240px" width="380" height="90" viewBox="0 0 380 90">
      <path d="M0 58 Q190 20 380 38 L380 90 L0 90 Z" fill="#fff"/>
      <path d="M0 58 Q190 20 380 38" fill="none" stroke="var(--orange)" stroke-width="5"/>
    </svg>
    <div class="seal" role="img" aria-label="Prüfzeichen-Siegel"><div class="seal__core"></div></div>

    <h1 class="cover-title">Hier wächst Mitsprache –<br>Ein Wegbericht zum Prüfzeichen</h1>

    <div class="partners">
      <div class="partner partner--main"><span class="partner__mark"></span>KWB</div>
      <div class="partner"><span class="partner__mark"></span>Jugendwerk Am Hang</div>
      <div class="partner"><span class="partner__mark"></span>Familienhaus Lindenhof</div>
      <div class="partner"><span class="partner__mark"></span>Kinderhilfe Talblick</div>
      <div class="partner"><span class="partner__mark"></span>Wohngruppen Seeblick</div>
    </div>
    <div class="partner abs" style="left:300px;top:490px"><span class="partner__mark"></span>Sozialwerk Brückenweg</div>
  </section>

</div>
</body>
</html>
```